Brightline Energy Product Distribution Brochure

We are looking to have our current brochure for our customers completely redesigned...the idea is to present the relevant information in an attractive way . Our website is brightlineenergyco.example where you can find more information about us. We have included a file with a rough idea of the page order and what each should include but feel free to adapt based on design. The example provided is only for context and doesnt have to be maintained. We will be using the brochure both digitally and in print form. As long as it reads easily and is eye catching, the design can be horizontal or vertical.Final deliverable should be indesign file.

"Our Brands" page: should be limited to one page (space being enough) where it has the header for each one (for example diesel generators) space for one or two lines of text and then the corresponding logos for each of the five categories
Updates

For those asking: the "our brands" page should be a single page layout where there is a header with the corresponding section and space for maybe one line of text followed by the two logos for that category. Each of the product pages should be similar in fashion to the one in the document attached: a photo of the product with some white space and space for the text to be included. We will be posting additional examples today

Target Market(s)

We want to present it to customers both digitally and in print so they can see our products

Industry/Entity Type

Power Generation

Font styles to use
Serif

Requirements
Must have
• Eye catching and able to present the information in a presentable fashion. Rest is up to you.
Nice to have
• Should incorporate the colors of our logo but can also add other depending on design

```html
<!DOCTYPE html>
<html lang="en">
<head>
<meta charset="utf-8">
<title>Brightline Energy – Distributor Program Guide</title>
<link rel="stylesheet" href="https://fonts.googleapis.com/css2?family=Libre+Baskerville:wght@400;700&family=Roboto+Slab:wght@400;700&display=swap">
<style>
:root{
  --yellow:#f6b90f;
  --gold:#f9c623;
  --charcoal:#3c3c3f;
  --ink:#2a2a2c;
  --page:#ececed;
  --page-shade:#d9d9db;
  --stage:#5b5b5d;
  --white:#ffffff;
  --muted:#6d6d70;
}
*{box-sizing:border-box;margin:0;padding:0}
html,body{width:1200px;height:1200px;overflow:hidden;background:var(--stage)}
body{position:relative;font-family:"Libre Baskerville",Georgia,serif;color:var(--ink)}
.spread{position:absolute;display:flex;box-shadow:0 4px 10px rgba(0,0,0,.35)}
.page{position:relative;overflow:hidden;background:linear-gradient(90deg,var(--page) 0%,#f4f4f5 60%,var(--page-shade) 100%)}
.page.right{background:linear-gradient(90deg,var(--page-shade) 0%,#f4f4f5 30%,var(--page) 100%)}
.abs{position:absolute}

/* cover */
.cover{left:278px;top:20px;width:650px;height:422px}
.cover .page{width:325px;height:422px}
.cover .band{position:absolute;left:0;right:0;bottom:0;height:92px;background:var(--charcoal);border-top:3px solid var(--yellow)}
.wordmark{font-family:"Libre Baskerville",serif;font-weight:400;letter-spacing:1px;color:var(--muted);display:flex;align-items:center;gap:5px;white-space:nowrap}
.wordmark .dot{width:9px;height:9px;background:var(--yellow)}
.cover .wordmark{font-size:9px;position:absolute;left:50%;transform:translateX(-50%)}
.contact{position:absolute;left:110px;font-family:"Roboto Slab",serif;font-weight:700;font-size:6.2px;color:var(--white);display:flex;align-items:center;gap:5px}
.contact svg{width:8px;height:8px}
.cover-photo{position:absolute;left:0;top:0;width:325px;height:330px;background:linear-gradient(180deg,#b8bcc0 0%,#9ea2a6 45%,#7d7f83 75%,#a89c86 100%)}
.genset-photo{position:absolute;background:linear-gradient(180deg,#f7f7f7 0%,#e2e2e2 70%,#2b2b2b 71%,#1d1d1d 100%);border-radius:2px}
.cover-title{position:absolute;right:22px;bottom:16px;text-align:right;color:var(--white)}
.cover-title h1{font-family:"Roboto Slab",serif;font-weight:700;font-size:22px;letter-spacing:.5px;line-height:1.05}
.cover-title h2{font-family:"Roboto Slab",serif;font-weight:400;font-size:19px;line-height:1.15}
.cover-title p{font-family:"Roboto Slab",serif;font-size:6.6px;color:var(--yellow);margin-top:5px}

/* interior */
.inner{width:533px;height:346px}
.inner .page{width:266.5px;height:346px}
.s1{left:52px;top:462px}.s2{left:614px;top:462px}.s3{left:52px;top:830px}.s4{left:614px;top:830px}
.topstrip{position:absolute;left:0;right:0;top:0;height:26px;background:var(--white)}
.topstrip::after{content:"";position:absolute;left:0;right:0;bottom:0;height:3px;background:linear-gradient(180deg,var(--ink) 50%,var(--yellow) 50%)}
.footstrip{position:absolute;left:0;right:0;bottom:0;height:26px;background:var(--white)}
.footstrip::before{content:"";position:absolute;left:0;right:0;top:0;height:3px;background:linear-gradient(180deg,var(--yellow) 50%,var(--ink) 50%)}
.running{position:absolute;font-family:"Libre Baskerville",serif;font-size:4.8px;font-weight:700;color:var(--ink);letter-spacing:.2px}
.running span{font-weight:400}
.folio{position:absolute;font-size:6px;font-weight:700}
.mini-mark{position:absolute;font-size:4px;color:var(--muted);display:flex;gap:2px;align-items:center}
.mini-mark i{width:5px;height:5px;background:var(--yellow);display:block}
.page-title{position:absolute;left:0;right:0;text-align:center;font-size:15.5px;font-weight:400;color:var(--ink)}
.page-title b{font-weight:700}
.stripes{position:absolute}

/* toc */
.toc{position:absolute;left:68px;top:98px;width:170px;list-style:none}
.toc li{display:flex;align-items:flex-end;height:18.1px;font-size:8px;font-weight:700}
.toc li span.n{width:16px}
.toc li span.l{flex:1;border-bottom:.5px solid #999;margin:0 4px 2px}
.toc li span.t{font-size:4.6px;font-weight:400;width:80px}

/* about */
.icon{position:absolute;width:34px;height:34px;border-radius:50%;background:var(--yellow);border:2px solid var(--ink)}
.copy{position:absolute;font-size:3.4px;line-height:1.35;color:var(--ink)}
.copy h4{font-size:3.4px;font-weight:700;text-transform:uppercase;margin-bottom:1px}
.copy ul{padding-left:6px}

/* brands */
.badge{position:absolute;width:82px;height:82px;border-radius:50%;background:var(--white);border:2.5px solid var(--charcoal)}
.badge .cap{position:absolute;top:14px;left:10px;right:10px;text-align:center;font-size:3.2px;line-height:1.3}
.ribbon{position:absolute;background:var(--charcoal);color:var(--yellow);font-family:"Roboto Slab",serif;font-size:5.4px;text-align:center;line-height:9px;height:9px;white-space:nowrap;clip-path:polygon(4% 0,96% 0,100% 50%,96% 100%,4% 100%,0 50%)}
.partner{position:absolute;background:#c9c9cc;border-radius:1px}
.para{position:absolute;font-size:3.3px;line-height:1.4;text-align:justify;color:#333}
.para p+p{margin-top:2px}

/* product pages */
.hero-disc{position:absolute;border-radius:50%;background:var(--yellow)}
.kw{position:absolute;font-family:"Roboto Slab",serif;font-weight:700;font-size:7px}
.brand-box{position:absolute;width:31px;height:24px;background:var(--white);border:1px solid var(--yellow);border-radius:3px}
.brand-box .nm{position:absolute;left:3px;top:3px;font-size:2.8px;color:var(--muted);white-space:nowrap}
.features{position:absolute;font-size:3.2px;line-height:1.55}
.features h5{font-size:4.2px;font-weight:700;margin-bottom:1px}
.features ul{padding-left:6px}
.stock-list{position:absolute;left:132px;top:98px;font-size:4.2px;line-height:11.5px;padding-left:6px}
.stock-thumb{position:absolute;width:48px;height:48px;border-radius:50%;border:2px solid var(--yellow);background:linear-gradient(180deg,#fafafa,#cfcfcf)}
</style>
</head>
<body>

<svg width="0" height="0" style="position:absolute">
  <defs>
    <linearGradient id="barY" x1="0" x2="1"><stop offset="0" stop-color="#f6b90f"/><stop offset="1" stop-color="#f9d65a"/></linearGradient>
    <linearGradient id="barK" x1="0" x2="1"><stop offset="0" stop-color="#2a2a2c"/><stop offset="1" stop-color="#8a8a8d" stop-opacity=".3"/></linearGradient>
    <linearGradient id="barK2" x1="1" x2="0"><stop offset="0" stop-color="#2a2a2c"/><stop offset="1" stop-color="#8a8a8d" stop-opacity=".3"/></linearGradient>
  </defs>
</svg>

<!-- COVER SPREAD -->
<section class="spread cover" aria-label="Cover">
  <div class="page back">
    <div class="wordmark" style="top:92px"><span class="dot"></span>BRIGHTLINE ENERGY</div>
    <svg class="stripes" style="left:0;top:205px" width="325" height="140" viewBox="0 0 325 140">
      <g>
        <rect x="0" y="10" width="130" height="5" fill="url(#barY)"/>
        <rect x="0" y="20" width="130" height="5" fill="url(#barK2)"/>
        <rect x="0" y="30" width="130" height="5" fill="url(#barY)"/>
        <rect x="0" y="40" width="130" height="5" fill="url(#barK2)"/>
        <polygon points="130,10 165,10 125,110 90,110" fill="#f6b90f" opacity=".85"/>
        <polygon points="150,10 160,10 120,110 110,110" fill="#fde26a"/>
        <rect x="95" y="85" width="230" height="5" fill="url(#barY)"/>
        <rect x="95" y="95" width="230" height="5" fill="#2a2a2c"/>
        <rect x="95" y="105" width="230" height="5" fill="url(#barY)"/>
        <rect x="95" y="115" width="230" height="5" fill="#2a2a2c"/>
        <rect x="95" y="125" width="230" height="5" fill="url(#barY)"/>
      </g>
    </svg>
    <div class="band">
      <div class="contact" style="top:24px">
        <svg viewBox="0 0 10 10"><path d="M5 0.5a3.2 3.2 0 0 1 3.2 3.2C8.2 6 5 9.5 5 9.5S1.8 6 1.8 3.7A3.2 3.2 0 0 1 5 .5z" fill="#f6b90f"/><circle cx="5" cy="3.7" r="1.2" fill="#3c3c3f"/></svg>
        4410 Harbor Line Ave, Tampa, FL 33602</div>
      <div class="contact" style="top:42px">
        <svg viewBox="0 0 10 10"><path d="M2 1l2 .2 1 2.4-1.2 1a5 5 0 0 0 2.6 2.6l1-1.2 2.4 1 .2 2C9.5 9.5 8 9.8 7 9.5A9 9 0 0 1 .5 3C.2 2 .5.5 2 1z" fill="#f6b90f"/></svg>
        1-800-555-0142 (Toll Free)</div>
      <div class="contact" style="top:60px">
        <svg viewBox="0 0 10 10"><circle cx="5" cy="5" r="4.3" fill="#f6b90f"/><path d="M1 5h8M5 .7c-2 2.5-2 6.1 0 8.6M5 .7c2 2.5 2 6.1 0 8.6" stroke="#3c3c3f" stroke-width=".6" fill="none"/></svg>
        www.brightlineenergyco.example</div>
    </div>
  </div>
  <div class="page front">
    <div class="cover-photo" role="img" aria-label="Night city skyline with light trails behind a white enclosed diesel generator"></div>
    <div class="genset-photo" style="left:93px;top:197px;width:180px;height:117px" role="img" aria-label="White soundproof generator set on a black base"></div>
    <div class="wordmark" style="top:101px;font-size:10px;color:#4a4a4d"><span class="dot"></span>BRIGHTLINE ENERGY</div>
    <svg class="stripes" style="left:0;top:237px" width="325" height="95" viewBox="0 0 325 95">
      <rect x="0" y="10" width="110" height="4" fill="url(#barY)"/>
      <rect x="0" y="18" width="100" height="4" fill="#2a2a2c" opacity=".7"/>
      <rect x="0" y="26" width="90" height="4" fill="url(#barY)"/>
      <rect x="0" y="34" width="80" height="4" fill="#2a2a2c" opacity=".6"/>
      <rect x="0" y="88" width="325" height="3" fill="#f6b90f"/>
    </svg>
    <div class="band">
      <div class="cover-title">
        <h1>DISTRIBUTOR</h1>
        <h2>PROGRAM GUIDE</h2>
        <p>DIESEL GENERATORS, ALTERNATORS &amp; PARTS</p>
      </div>
    </div>
  </div>
</section>

<!-- SPREAD 1: contents / about -->
<section class="spread inner s1" aria-label="Contents and company">
  <div class="page left">
    <div class="topstrip"></div>
    <h2 class="page-title" style="top:52px">Table of <b>Contents</b></h2>
    <ol class="toc">
      <li><span class="n">01</span><span class="l"></span><span class="t">ABOUT OUR COMPANY</span></li>
      <li><span class="n">02</span><span class="l"></span><span class="t">OUR BRANDS</span></li>
      <li><span class="n">04</span><span class="l"></span><span class="t">OUR STOCK</span></li>
      <li><span class="n">05</span><span class="l"></span><span class="t">STANDBY GENERATORS</span></li>
      <li><span class="n">06</span><span class="l"></span><span class="t">PRIME GENERATORS</span></li>
      <li><span class="n">07</span><span class="l"></span><span class="t">RENTAL GENERATORS</span></li>
      <li><span class="n">08</span><span class="l"></span><span class="t">AC ALTERNATORS</span></li>
      <li><span class="n">09</span><span class="l"></span><span class="t">ALTERNATOR PARTS</span></li>
      <li><span class="n">10</span><span class="l"></span><span class="t">CONTROLLERS</span></li>
      <li><span class="n">11</span><span class="l"></span><span class="t">TRANSFER SWITCHES</span></li>
      <li><span class="n">12</span><span class="l"></span><span class="t">OUR DISTRIBUTORS</span></li>
    </ol>
    <svg class="stripes" style="left:0;top:300px" width="266" height="20" viewBox="0 0 266 20">
      <rect x="0" y="2" width="90" height="3" fill="url(#barY)"/><rect x="0" y="7" width="90" height="3" fill="#2a2a2c"/>
      <rect x="96" y="9" width="170" height="3" fill="url(#barK)"/><rect x="96" y="14" width="170" height="3" fill="url(#barY)"/>
      <polygon points="88,0 96,0 100,18 92,18" fill="#f6b90f"/>
    </svg>
    <div class="footstrip"></div>
  </div>
  <div class="page right">
    <div class="topstrip"></div>
    <div class="mini-mark" style="right:14px;top:13px"><i></i>BRIGHTLINE ENERGY</div>
    <h2 class="page-title" style="top:52px">About our <b>Company</b></h2>
    <div class="icon" style="left:46px;top:76px"></div>
    <div class="copy" style="left:88px;top:80px;width:128px">Brightline Energy is a Florida based company specializing in diesel generators, transfer switches, alternators and parts for the power industry.</div>
    <div class="icon" style="left:190px;top:122px"></div>
    <div class="copy" style="left:58px;top:112px;width:128px"><h4>For power generation we can start by offering a team of experts</h4><ul><li>Top rated by business bureau</li><li>Over 40 years combined industry experience</li><li>Products shipped worldwide every month</li><li>Certified by electrical systems groups</li></ul></div>
    <div class="icon" style="left:46px;top:167px"></div>
    <div class="copy" style="left:88px;top:170px;width:128px"><h4>We know your urgency, so we keep stock ready</h4><ul><li>Generators from 20 to 2000 kW in stock</li><li>Fuel tanks from 50 to 1000 gallons</li><li>Transfer switches from 100 to 2000 amps</li></ul></div>
    <div class="icon" style="left:190px;top:213px"></div>
    <div class="copy" style="left:58px;top:217px;width:128px"><h4>Our products are purchased directly from the maker</h4><ul><li>Every unit is fully traceable</li><li>Origin certified on request</li></ul></div>
    <div class="icon" style="left:46px;top:258px"></div>
    <div class="copy" style="left:88px;top:260px;width:128px"><h4>One single source for cost, lead time and logistics</h4><ul><li>Diesel Generators</li><li>AC Alternators</li><li>Transfer Switches</li><li>Voltage Regulators</li><li>Fuel Tanks</li><li>Engine Parts</li></ul></div>
    <div class="footstrip"><span class="running" style="left:92px;top:11px">DISTRIBUTOR <span>PROGRAM GUIDE</span></span><span class="folio" style="right:24px;top:9px">1</span></div>
  </div>
</section>

<!-- SPREAD 2: brands -->
<section class="spread inner s2" aria-label="Our brands">
  <div class="page left">
    <div class="topstrip"><span class="folio" style="left:26px;top:9px">2</span><span class="running" style="left:92px;top:11px">DISTRIBUTOR <span>PROGRAM GUIDE</span></span></div>
    <h2 class="page-title" style="top:52px;left:-70px">Our <b>Brands</b></h2>
    <div class="badge" style="left:36px;top:82px"><div class="cap">Trusted partner for reliable power</div><div class="partner" style="left:24px;top:50px;width:28px;height:6px"></div><div class="partner" style="left:24px;top:60px;width:20px;height:5px"></div></div>
    <div class="ribbon" style="left:28px;top:112px;width:98px">DIESEL GENERATORS</div>
    <div class="para" style="left:130px;top:92px;width:116px"><p>Our diesel generator line pairs proven engines with dependable alternators, delivering steady power for hospitals, data centers, farms and job sites.</p><p>Every unit is tested before shipping and backed by our service team, so installers receive equipment ready to run on day one.</p></div>
    <div class="para" style="left:20px;top:200px;width:116px"><p>We stock complete alternators and spare parts, including rotors, stators, bearings and regulators, to keep field repairs short and simple.</p><p>Our specialists help match each replacement part to the right frame size, winding and voltage for your machine.</p></div>
    <div class="badge" style="left:160px;top:194px"><div class="cap">Trusted partner for reliable power</div><div class="partner" style="left:22px;top:48px;width:32px;height:5px"></div><div class="partner" style="left:26px;top:58px;width:26px;height:6px"></div></div>
    <div class="ribbon" style="left:150px;top:224px;width:102px">AC ALTERNATORS &amp; PARTS</div>
    <svg class="stripes" style="left:0;top:300px" width="266" height="20" viewBox="0 0 266 20">
      <rect x="0" y="2" width="90" height="3" fill="url(#barY)"/><rect x="0" y="7" width="90" height="3" fill="#2a2a2c"/>
      <rect x="96" y="9" width="170" height="3" fill="url(#barK)"/><rect x="96" y="14" width="170" height="3" fill="url(#barY)"/>
      <polygon points="88,0 96,0 100,18 92,18" fill="#f6b90f"/>
    </svg>
    <div class="footstrip"><div class="mini-mark" style="left:14px;top:12px"><i></i>BRIGHTLINE ENERGY</div></div>
  </div>
  <div class="page right">
    <div class="topstrip"><div class="mini-mark" style="right:14px;top:13px"><i></i>BRIGHTLINE ENERGY</div></div>
    <div class="badge" style="left:36px;top:82px"><div class="cap">Trusted partner for reliable power</div><div class="partner" style="left:22px;top:48px;width:32px;height:5px"></div><div class="partner" style="left:28px;top:58px;width:20px;height:7px"></div></div>
    <div class="ribbon" style="left:28px;top:112px;width:98px">TRANSFER SWITCHES</div>
    <div class="para" style="left:130px;top:92px;width:116px"><p>Automatic and manual transfer switches move your load between utility and generator power safely, quickly and without interruption.</p><p>Open and closed transition models are available in a wide range of amperage ratings for every size of site.</p></div>
    <div class="para" style="left:20px;top:200px;width:116px"><p>Digital controllers give operators full command of start, stop, monitoring and protection from one clear front panel.</p><p>Units support remote access, paralleling and load sharing, and each one arrives programmed to the settings you need.</p></div>
    <div class="badge" style="left:160px;top:194px"><div class="cap">Trusted partner for reliable power</div><div class="partner" style="left:24px;top:46px;width:28px;height:6px"></div><div class="partner" style="left:31px;top:56px;width:14px;height:12px;background:#2a2a2c"></div></div>
    <div class="ribbon" style="left:150px;top:224px;width:102px">CONTROLS</div>
    <div class="footstrip"><span class="running" style="left:92px;top:11px">DISTRIBUTOR <span>PROGRAM GUIDE</span></span><span class="folio" style="right:24px;top:9px">3</span></div>
  </div>
</section>

<!-- SPREAD 3: stock / standby -->
<section class="spread inner s3" aria-label="Our stock and standby generators">
  <div class="page left">
    <div class="topstrip"><span class="folio" style="left:26px;top:9px">4</span><span class="running" style="left:92px;top:11px">DISTRIBUTOR <span>PROGRAM GUIDE</span></span></div>
    <svg class="abs" style="left:0;top:30px" width="80" height="290" viewBox="0 0 80 290"><path d="M0 10 C60 60 70 180 10 285" stroke="#f6b90f" stroke-width="2" fill="none"/><path d="M0 40 C45 90 50 190 0 260" stroke="#f9d65a" stroke-width="1" fill="none"/></svg>
    <h2 class="page-title" style="top:52px;left:0">Our <b>Stock</b></h2>
    <div class="ribbon" style="left:94px;top:78px;width:92px">OUR PRODUCTS</div>
    <div class="stock-thumb" style="left:26px;top:76px" role="img" aria-label="Generator set"></div>
    <div class="stock-thumb" style="left:26px;top:132px" role="img" aria-label="Trailer mounted generator"></div>
    <div class="stock-thumb" style="left:26px;top:188px;background:linear-gradient(180deg,#555,#1e1e1e)" role="img" aria-label="Alternator"></div>
    <div class="stock-thumb" style="left:26px;top:244px;background:linear-gradient(180deg,#444,#1a1a1a)" role="img" aria-label="Generator control panel"></div>
    <ul class="stock-list">
      <li>Automatic Voltage Regulators</li><li>AC Alternators</li><li>Alternator Parts</li><li>Diesel Generators</li><li>Transfer Switches</li><li>Battery Chargers</li><li>Generator Control Panels</li><li>Generator Ends</li><li>Plantas electricas GAS</li><li>Generadores a GAS</li><li>Plantas electricas diesel</li><li>Tableros de Transferencia</li>
    </ul>
    <div class="para" style="left:104px;top:256px;width:140px"><p>Knowing the right product for your needs is not enough in a demanding market; it is key to have stock at hand when needed.</p><p>Brightline Energy keeps one of the largest parts stocks in the region, ready to ship the same day.</p></div>
    <div class="footstrip"><div class="mini-mark" style="left:14px;top:12px"><i></i>BRIGHTLINE ENERGY</div></div>
  </div>
  <div class="page right">
    <div class="topstrip"><div class="mini-mark" style="right:14px;top:13px"><i></i>BRIGHTLINE ENERGY</div></div>
    <h2 class="page-title" style="top:52px">Diesel <b style="font-weight:400">Generators</b></h2>
    <svg class="abs" style="left:200px;top:80px" width="66" height="240" viewBox="0 0 66 240"><path d="M66 0 C10 60 20 160 -10 240" stroke="#f6b90f" stroke-width="2" fill="none"/><path d="M66 30 C30 80 40 170 10 240" stroke="#f9d65a" stroke-width="1" fill="none"/></svg>
    <div class="hero-disc" style="left:44px;top:78px;width:112px;height:112px"></div>
    <div class="genset-photo" style="left:32px;top:104px;width:140px;height:82px" role="img" aria-label="Standby diesel generator in white enclosure"></div>
    <div class="kw" style="left:146px;top:106px">100 KW</div>
    <div class="ribbon" style="left:32px;top:80px;width:92px">STANDBY GENERATORS</div>
    <div class="brand-box" style="left:190px;top:98px"><span class="nm">Brightline Energy</span><div class="partner" style="left:7px;top:11px;width:16px;height:4px"></div><div class="partner" style="left:7px;top:17px;width:12px;height:3px"></div></div>
    <div class="features" style="left:32px;top:206px;width:180px"><h5>FEATURES:</h5><ul>
      <li>20 to 100 kW diesel engine, Tier 3</li><li>Brushless alternator with digital regulator</li><li>Digital controller for stand-alone operation</li><li>Sound attenuated steel enclosure</li><li>Main line circuit breaker</li><li>Skid mounted double wall fuel tank</li><li>Battery disconnect switch</li><li>12V starting battery</li></ul></div>
    <div class="footstrip"><span class="running" style="left:92px;top:11px">DISTRIBUTOR <span>PROGRAM GUIDE</span></span><span class="folio" style="right:24px;top:9px">5</span></div>
  </div>
</section>

<!-- SPREAD 4: prime / rental -->
<section class="spread inner s4" aria-label="Prime and rental generators">
  <div class="page left">
    <div class="topstrip"><span class="folio" style="left:26px;top:9px">6</span><span class="running" style="left:92px;top:11px">DISTRIBUTOR <span>PROGRAM GUIDE</span></span></div>
    <h2 class="page-title" style="top:52px">Diesel <b style="font-weight:400">Generators</b></h2>
    <svg class="abs" style="left:200px;top:80px" width="66" height="240" viewBox="0 0 66 240"><path d="M66 0 C10 60 20 160 -10 240" stroke="#f6b90f" stroke-width="2" fill="none"/><path d="M66 30 C30 80 40 170 10 240" stroke="#f9d65a" stroke-width="1" fill="none"/></svg>
    <div class="hero-disc" style="left:44px;top:78px;width:112px;height:112px"></div>
    <div class="genset-photo" style="left:32px;top:104px;width:140px;height:82px" role="img" aria-label="Prime power diesel generator in white enclosure"></div>
    <div class="kw" style="left:146px;top:106px">100 KW</div>
    <div class="ribbon" style="left:32px;top:80px;width:92px">PRIME GENERATORS</div>
    <div class="brand-box" style="left:190px;top:98px"><span class="nm">Brightline Energy</span><div class="partner" style="left:7px;top:11px;width:16px;height:4px"></div><div class="partner" style="left:7px;top:17px;width:12px;height:3px"></div></div>
    <div class="features" style="left:32px;top:206px;width:180px"><h5>FEATURES:</h5><ul>
      <li>20 to 100 kW diesel engine, Tier 3</li><li>Brushless alternator with digital regulator</li><li>Digital controller for stand-alone operation</li><li>Sound attenuated steel enclosure</li><li>Main line circuit breaker</li><li>Skid mounted double wall fuel tank</li><li>Battery disconnect switch</li><li>12V starting battery</li></ul></div>
    <div class="footstrip"><div class="mini-mark" style="left:14px;top:12px"><i></i>BRIGHTLINE ENERGY</div></div>
  </div>
  <div class="page right">
    <div class="topstrip"><div class="mini-mark" style="right:14px;top:13px"><i></i>BRIGHTLINE ENERGY</div></div>
    <h2 class="page-title" style="top:52px">Diesel <b style="font-weight:400">Generators</b></h2>
    <svg class="abs" style="left:200px;top:80px" width="66" height="240" viewBox="0 0 66 240"><path d="M66 0 C10 60 20 160 -10 240" stroke="#f6b90f" stroke-width="2" fill="none"/><path d="M66 30 C30 80 40 170 10 240" stroke="#f9d65a" stroke-width="1" fill="none"/></svg>
    <div class="hero-disc" style="left:30px;top:76px;width:130px;height:130px"></div>
    <div class="genset-photo" style="left:48px;top:96px;width:96px;height:92px;background:linear-gradient(180deg,#f4f4f4 0%,#dcdcdc 60%,#262626 61%,#111 100%)" role="img" aria-label="Trailer mounted rental diesel generator"></div>
    <div class="ribbon" style="left:32px;top:80px;width:92px">RENTAL GENERATORS</div>
    <div class="brand-box" style="left:190px;top:98px"><span class="nm">Brightline Energy</span><div class="partner" style="left:7px;top:11px;width:16px;height:4px"></div><div class="partner" style="left:7px;top:17px;width:12px;height:3px"></div></div>
    <div class="features" style="left:32px;top:212px;width:180px"><h5>FEATURES:</h5><ul>
      <li>20 to 100 kW diesel engine, Tier 3</li><li>Brushless alternator with digital regulator</li><li>Digital controller for stand-alone operation</li><li>Sound attenuated steel enclosure</li><li>Main line circuit breaker</li><li>Skid mounted double wall fuel tank</li><li>Battery disconnect switch</li><li>12V starting battery</li></ul></div>
    <div class="footstrip"><span class="running" style="left:92px;top:11px">DISTRIBUTOR <span>PROGRAM GUIDE</span></span><span class="folio" style="right:24px;top:9px">7</span></div>
  </div>
</section>

</body>
</html>
```